We are a local Communty Pharmacy wishing to promote and market a specialised Pharmaceutical Service

We would like a design that is professional and enticing ( according to the brief In attached files)
We wish to Market Compounding Pharmacy as a specialist side of our business.
We have the expertise a purpose built preparation laboratory.
The main purpose is an Internet presence that entices prospective patients to contact or visit our physical store.

Target Market(s)

Patients Medicos and Veterinary clients

Industry/Entity Type

Pharmacy

Coding

Coded - Design and coding required

Number of Pages Required

1 page

Requirements
Must have
• Clear friendly image
Nice to have
• soft enticing feel
Should not have
• No crass loud unprofessional elements

```html
<!DOCTYPE html>
<html lang="en">
<head>
<meta charset="utf-8">
<title>Meridale Compounding Pharmacy</title>
<link rel="stylesheet" href="https://fonts.googleapis.com/css2?family=Lato:wght@300;400;700;900&family=Open+Sans:wght@400;600;700&display=swap">
<style>
:root{
  --navy:#1f3f74;
  --blue:#2a6fb3;
  --band:#2f79bd;
  --yellow:#f4c21b;
  --green:#2fa84f;
  --orange:#f0a21a;
  --ink:#333a42;
  --muted:#7a8088;
  --line:#e3e5e8;
  --footer:#f1f1f1;
  --footbar:#e4e4e4;
}
*{box-sizing:border-box;margin:0;padding:0}
html,body{width:1200px;height:2348px;overflow:hidden;background:#fff}
body{font-family:"Lato",sans-serif;color:var(--ink);position:relative}
.wrap{width:840px;margin:0 auto;position:relative}

/* header */
.site-header{height:88px;border-bottom:1px solid var(--line);position:relative}
.main-nav{position:absolute;left:180px;top:6px;display:flex;gap:22px;font-size:11px;font-weight:700;color:var(--ink)}
.main-nav a{color:inherit;text-decoration:none}
.main-nav a.active{color:var(--blue)}
.brand{position:absolute;left:186px;top:32px;display:flex;align-items:center;gap:8px}
.brand-mark{width:26px;height:26px;background:var(--navy)}
.brand-name{font-family:"Open Sans",sans-serif;font-weight:700;font-size:15px;color:var(--navy);line-height:1.05;width:150px}
.head-contact{position:absolute;left:440px;top:30px;font-size:10px;color:var(--muted);line-height:16px;display:flex;gap:8px}
.head-address{position:absolute;left:916px;top:30px;font-size:10px;color:var(--muted);line-height:14px;display:flex;gap:8px;width:250px}
.head-address b{color:var(--ink);font-weight:700}
.ico{flex:none}

/* hero */
.hero{height:432px;position:relative;overflow:hidden}
.hero-photo{position:absolute;inset:0;background:linear-gradient(100deg,#e3e5e3 0%,#eef0ed 40%,#f4f5f1 62%,#dde4d6 100%)}
.hero-tag{position:absolute;left:108px;top:184px;background:var(--yellow);padding:14px 22px 14px 72px;font-family:"Open Sans",sans-serif;font-weight:700;font-size:18px;color:var(--navy);letter-spacing:.3px}
.hero-tag:before{content:"";position:absolute;left:20px;top:8px;width:38px;height:38px;background:#fff;border-radius:50%}
.hero-strip{position:absolute;left:148px;top:284px;background:var(--green);color:#fff;font-size:11px;font-weight:700;letter-spacing:.6px;padding:7px 22px}
.btn{display:inline-block;font-size:10px;font-weight:700;letter-spacing:.5px;text-transform:uppercase;color:#fff;padding:9px 18px;text-decoration:none}
.btn-navy{background:var(--navy)}
.btn-grey{background:#5c6168}
.btn-orange{background:var(--orange)}
.btn-outline{border:1px solid #fff}
.hero .btn{position:absolute;left:226px;top:362px;padding:10px 22px}
.hero-arrow{position:absolute;top:250px;width:22px;height:34px;background:rgba(0,0,0,.18);display:flex;align-items:center;justify-content:center}
.hero-arrow.l{left:0}.hero-arrow.r{right:0}
.dots{position:absolute;left:0;right:0;top:404px;display:flex;justify-content:center;gap:6px}
.dots i{width:7px;height:7px;border-radius:50%;background:#c3c6c9}
.dots i.on{background:var(--blue)}

/* about */
.about{padding-top:32px;text-align:center;height:430px}
.section-title{font-family:"Open Sans",sans-serif;font-weight:700;font-size:21px;color:#2b3138;letter-spacing:.2px}
.rule{width:44px;height:3px;background:var(--blue);margin:8px auto 0}
.about p{margin:24px auto 0;font-size:11.5px;line-height:19px;color:var(--muted);text-align:justify;width:840px}
.about .actions{margin-top:36px;display:flex;justify-content:center;gap:10px}

/* features */
.features{text-align:center;height:372px}
.feature-grid{display:flex;justify-content:space-between;width:840px;margin:36px auto 0}
.feature{width:272px}
.feature-img{height:168px}
.f1{background:linear-gradient(135deg,#c9d6e2,#eef1f4 60%,#b9c8d6)}
.f2{background:linear-gradient(135deg,#d9c6b8,#f3ebe5 55%,#b7c9d6)}
.f3{background:linear-gradient(135deg,#b8323a,#e9e6e6 55%,#d6d9dd)}
.feature h3{margin-top:24px;font-family:"Open Sans",sans-serif;font-size:15px;font-weight:700;color:#2b3138;text-transform:uppercase}

/* band */
.band{height:220px;background:var(--band);text-align:center;color:#fff;padding-top:80px}
.band h2{font-family:"Open Sans",sans-serif;font-size:22px;font-weight:400;letter-spacing:.2px}
.band h2 b{font-weight:700;color:var(--yellow)}
.band p{font-size:11px;opacity:.85;margin-top:10px}
.band .actions{margin-top:18px;display:flex;justify-content:center;gap:10px}

/* info */
.info{height:420px;padding-top:68px}
.info-grid{display:flex;justify-content:space-between;width:840px;margin:0 auto}
.info-col{width:260px}
.info-col h3{display:flex;align-items:center;gap:10px;font-family:"Open Sans",sans-serif;font-weight:400;font-size:22px;color:#3a4048;padding-bottom:12px;border-bottom:1px solid var(--line)}
.map{height:170px;margin-top:16px;background:linear-gradient(135deg,#e8ecdf,#dfe6ee 60%,#eef0e8)}
.hours{margin-top:14px;font-size:10.5px}
.hours h4{font-size:11px;font-weight:900;margin-bottom:6px}
.hours table{width:100%;border-collapse:collapse}
.hours td{padding:3px 0;color:var(--muted)}
.hours td:first-child{font-weight:700;color:var(--ink)}
.reach{margin-top:16px;font-size:10.5px;color:var(--muted);line-height:15px}
.reach li{list-style:none;display:flex;gap:10px;margin-bottom:12px}
.socials{display:flex;gap:8px;margin-top:4px}
.socials i{width:14px;height:14px;border-radius:50%;background:#5c6168}

/* footer */
.site-footer{height:348px;background:var(--footer);padding-top:56px}
.foot-grid{display:flex;width:840px;margin:0 auto}
.foot-grid h4{font-family:"Open Sans",sans-serif;font-size:12px;font-weight:700;letter-spacing:.6px;text-transform:uppercase;color:#2b3138;margin-bottom:16px}
.foot-menu{width:150px}
.foot-menu li{list-style:none;font-size:10.5px;color:var(--muted);line-height:19px}
.foot-news{width:420px}
.news-item{display:flex;gap:12px;margin-bottom:20px}
.news-thumb{width:52px;height:44px;flex:none;background:linear-gradient(135deg,#c9cfd6,#eceef0)}
.news-item p{font-size:10.5px;color:var(--ink);line-height:15px;width:160px}
.news-item small{display:block;font-size:9.5px;color:var(--muted);margin-top:3px}
.foot-quick{margin-left:auto;width:220px}
.field{height:26px;background:#fff;border:1px solid #dcdcdc;margin-bottom:6px;font-size:10px;color:#9a9fa5;padding:6px 8px}
.field.tall{height:54px}
.foot-quick .btn{display:block;text-align:center;background:var(--green);margin-top:4px}
.foot-bar{position:absolute;left:0;right:0;top:2300px;height:48px;background:var(--footbar)}
.foot-bar .wrap{display:flex;justify-content:space-between;align-items:center;height:48px;font-size:10px;color:var(--muted)}
.foot-bar .socials i{background:#9aa0a6;width:12px;height:12px}
</style>
</head>
<body>

<header class="site-header">
  <nav class="main-nav">
    <a class="active">Home</a><a>About us</a><a>Locations</a><a>Timings</a><a>Contact</a>
  </nav>
  <div class="brand">
    <span class="brand-mark"></span>
    <span class="brand-name">Meridale Compounding Pharmacy</span>
  </div>
  <div class="head-contact">
    <svg class="ico" width="14" height="14" viewBox="0 0 14 14"><circle cx="7" cy="7" r="7" fill="#1f3f74"/><path d="M4 5h6v4H4z" fill="none" stroke="#fff" stroke-width="1"/><path d="M4 5l3 2 3-2" fill="none" stroke="#fff" stroke-width="1"/></svg>
    <div>care@meridalepharmacy.com<br>Tel: (08) 5550 1824<br>Phone: (08) 5550 1825</div>
  </div>
  <div class="head-address">
    <svg class="ico" width="14" height="14" viewBox="0 0 14 14"><circle cx="7" cy="7" r="7" fill="#1f3f74"/><path d="M7 3.5a2.3 2.3 0 0 1 2.3 2.3C9.3 7.6 7 10.5 7 10.5S4.7 7.6 4.7 5.8A2.3 2.3 0 0 1 7 3.5z" fill="#fff"/></svg>
    <div><b>MERIDALE COMPOUNDING PHARMACY</b><br>Shop 4, 210 Linden Road, Meridale<br>WA 6099 AUSTRALIA</div>
  </div>
</header>

<section class="hero">
  <div class="hero-photo" role="img" aria-label="Photo: white mortar and pestle with fresh green herbs on a light background"></div>
  <div class="hero-tag">COMPOUNDING PHARMACY</div>
  <div class="hero-strip">A CUSTOMISED MEDICATIONS FOR PATIENTS</div>
  <a class="btn btn-navy">Contact Now</a>
  <span class="hero-arrow l"><svg width="8" height="12" viewBox="0 0 8 12"><path d="M6 1L1 6l5 5" stroke="#fff" stroke-width="2" fill="none"/></svg></span>
  <span class="hero-arrow r"><svg width="8" height="12" viewBox="0 0 8 12"><path d="M2 1l5 5-5 5" stroke="#fff" stroke-width="2" fill="none"/></svg></span>
  <div class="dots"><i class="on"></i><i></i><i></i></div>
</section>

<section class="about">
  <h2 class="section-title">WHAT IS COMPOUNDING PHARMACY?</h2>
  <div class="rule"></div>
  <p>Compounding is the art and science of preparing personalised medicines for patients whose needs cannot be met by commercially available products. Our pharmacists work closely with doctors, specialists and veterinarians to prepare a dose, strength or form that suits each person. Medicines can be made free of dyes, gluten, lactose or preservatives, flavoured for children and pets, or changed into creams, gels, capsules, lozenges and liquids that are easier to take. Every preparation is made to order in our purpose built laboratory using quality ingredients and strict procedures. We are proud to help patients who struggle with swallowing tablets, need rare dosages, or react to common fillers. Talk to our friendly team about how a compounded medicine could help you, your family or your animal companions, and visit our store today.</p>
  <div class="actions"><a class="btn btn-navy">Contact Now</a><a class="btn btn-grey">Read More</a></div>
</section>

<section class="features">
  <h2 class="section-title">FEATURE ITEMS</h2>
  <div class="rule"></div>
  <div class="feature-grid">
    <div class="feature"><div class="feature-img f1" role="img" aria-label="Photo: veterinarian examining a pet"></div><h3>Vet Article</h3></div>
    <div class="feature"><div class="feature-img f2" role="img" aria-label="Photo: skin care treatment for scars"></div><h3>Scar Therapy</h3></div>
    <div class="feature"><div class="feature-img f3" role="img" aria-label="Photo: laboratory blood sample tubes"></div><h3>Thyroid Extract</h3></div>
  </div>
</section>

<section class="band">
  <h2><b>COMPOUNDING</b> is <b>CUSTOMISED MEDICATIONS</b> for <b>PATIENTS</b></h2>
  <p>Each preparation is made to order in our own laboratory, prepared by qualified pharmacists and tailored to the exact needs of every patient we serve.</p>
  <div class="actions"><a class="btn btn-orange">Contact Now</a><a class="btn btn-outline">Read More</a></div>
</section>

<section class="info">
  <div class="info-grid">
    <div class="info-col">
      <h3><svg width="18" height="22" viewBox="0 0 18 22"><path d="M9 1a7 7 0 0 1 7 7c0 5-7 13-7 13S2 13 2 8a7 7 0 0 1 7-7z" fill="#2a6fb3"/><circle cx="9" cy="8" r="2.6" fill="#fff"/></svg>Where we are</h3>
      <div class="map" role="img" aria-label="Street map showing the pharmacy location"></div>
    </div>
    <div class="info-col">
      <h3><svg width="22" height="22" viewBox="0 0 22 22"><circle cx="11" cy="11" r="9.5" fill="none" stroke="#2a6fb3" stroke-width="2"/><path d="M11 5v6l4 3" stroke="#2a6fb3" stroke-width="2" fill="none"/></svg>Our timings</h3>
      <div class="hours">
        <h4>7 DAYS A WEEK</h4>
        <table>
          <tr><td>Monday</td><td>8:30 am – 7:00 pm</td></tr>
          <tr><td>Tuesday</td><td>8:30 am – 7:00 pm</td></tr>
          <tr><td>Wednesday</td><td>8:30 am – 7:00 pm</td></tr>
          <tr><td>Thursday</td><td>8:30 am – 9:00 pm</td></tr>
          <tr><td>Friday</td><td>8:30 am – 7:00 pm</td></tr>
          <tr><td>Saturday</td><td>9:00 am – 5:00 pm</td></tr>
          <tr><td>Sunday</td><td>10:00 am – 4:00 pm</td></tr>
        </table>
      </div>
    </div>
    <div class="info-col">
      <h3><svg width="22" height="20" viewBox="0 0 22 20"><path d="M2 10l6 6L20 3" stroke="#2a6fb3" stroke-width="3" fill="none"/></svg>How to reach us</h3>
      <ul class="reach">
        <li><svg class="ico" width="14" height="14" viewBox="0 0 14 14"><rect x="1" y="3" width="12" height="8" fill="none" stroke="#5c6168"/><path d="M1 3l6 4 6-4" fill="none" stroke="#5c6168"/></svg>care@meridalepharmacy.com</li>
        <li><svg class="ico" width="14" height="14" viewBox="0 0 14 14"><path d="M3 1h3l1 3-2 1a8 8 0 0 0 4 4l1-2 3 1v3a1 1 0 0 1-1 1A11 11 0 0 1 2 2a1 1 0 0 1 1-1z" fill="#5c6168"/></svg>(08) 5550 1824<br>(08) 5550 1825</li>
        <li><svg class="ico" width="14" height="14" viewBox="0 0 14 14"><path d="M7 1a4.5 4.5 0 0 1 4.5 4.5C11.5 9 7 13 7 13S2.5 9 2.5 5.5A4.5 4.5 0 0 1 7 1z" fill="#5c6168"/></svg>Shop 4, 210 Linden Road,<br>Meridale WA 6099</li>
      </ul>
      <div class="socials"><i></i><i></i><i></i><i></i><i></i></div>
    </div>
  </div>
</section>

<footer class="site-footer">
  <div class="foot-grid">
    <div class="foot-menu">
      <h4>Menu</h4>
      <ul><li>Home</li><li>About us</li><li>Locations</li><li>Timings</li><li>Contact</li></ul>
    </div>
    <div class="foot-news">
      <h4>Latest News</h4>
      <div class="news-item"><div class="news-thumb" role="img" aria-label="Photo: skin care product"></div><p>Fresh preparations for skin care now available in store<small>12 March 2024</small></p></div>
      <div class="news-item"><div class="news-thumb" role="img" aria-label="Photo: pharmacist preparing medicine"></div><p>Veterinary compounding for cats and dogs explained simply<small>28 February 2024</small></p></div>
    </div>
    <div class="foot-quick">
      <h4>Quick Contact Us</h4>
      <div class="field">Name</div>
      <div class="field">Email</div>
      <div class="field tall">Message</div>
      <a class="btn">Send It Now</a>
    </div>
  </div>
</footer>
<div class="foot-bar">
  <div class="wrap">
    <span>Copyright 2024 Meridale Compounding Pharmacy. All rights reserved.</span>
    <div class="socials"><i></i><i></i><i></i><i></i><i></i><i></i></div>
  </div>
</div>

</body>
</html>
```